We need a card and logo design for a new business based in Dallas Texas called Stonemarsh Financial LLC.

We provide bridge loans.We offer pay day loans,title loans and check cashing.Our products are emmergency loans that help borrowers meet short term liquidity needs until the next pay check.

The final design should communicate,professionalism,Sophistication and friendliness to our customers.Use the color Blue as much as possible and another eye catching color if possible.We will consider a profesional looking knight logo with the color Blue in it.Please design a full corporate identity.

```html
<!DOCTYPE html>
<html lang="en">
<head>
<meta charset="utf-8">
<title>Stonemarsh Financial LLC – Business Card</title>
<link rel="stylesheet" href="https://fonts.googleapis.com/css2?family=Roboto+Slab:wght@300;400;600&display=swap">
<style>
  :root {
    --page-bg: #ebe7e1;
    --card-white: #ffffff;
    --blue-light: #0d86b4;
    --blue-mid: #146f9c;
    --blue-deep: #1d4f7d;
    --ink-on-blue: #ffffff;
    --logo-blue: #1a6fa3;
    --card-shadow: rgba(40, 30, 20, 0.22);
  }
  * { margin: 0; padding: 0; box-sizing: border-box; }
  html, body {
    width: 1200px;
    height: 1200px;
    overflow: hidden;
    background: var(--page-bg);
    font-family: "Roboto Slab", Georgia, serif;
  }
  .canvas {
    width: 1200px;
    height: 1200px;
    display: flex;
    flex-direction: column;
    align-items: center;
    justify-content: center;
    gap: 70px;
  }
  .card {
    position: relative;
    width: 840px;
    height: 480px;
    overflow: hidden;
    box-shadow: 0 10px 28px var(--card-shadow);
  }

  /* Front side */
  .card--front { background: var(--card-white); }
  .card--front .blue-band {
    position: absolute;
    left: 0; right: 0; bottom: 0;
    height: 62%;
    background: linear-gradient(180deg, var(--blue-light) 0%, var(--blue-mid) 45%, var(--blue-deep) 100%);
  }
  .wordmark {
    text-align: center;
    font-weight: 400;
    line-height: 1.05;
    letter-spacing: 0.06em;
  }
  .wordmark__name { display: block; text-transform: uppercase; font-size: 30px; }
  .wordmark__suffix { display: block; font-size: 22px; letter-spacing: 0.08em; }
  .wordmark__mark {
    display: block;
    width: 14px; height: 14px;
    margin: 0 auto 10px;
  }
  .card--front .wordmark {
    position: absolute;
    top: 70px;
    left: 50%;
    transform: translateX(-50%);
    color: var(--logo-blue);
    white-space: nowrap;
  }
  .card--front .wordmark__mark { background: var(--logo-blue); }

  .holder {
    position: absolute;
    top: 212px;
    left: 50%;
    transform: translateX(-50%);
    text-align: left;
    color: var(--ink-on-blue);
    font-weight: 300;
    font-size: 16px;
    line-height: 1.35;
    letter-spacing: 0.02em;
    white-space: nowrap;
  }
  .holder__name { text-transform: uppercase; }
  .contact {
    position: absolute;
    top: 212px;
    right: 44px;
    text-align: right;
    color: var(--ink-on-blue);
    font-weight: 300;
    font-size: 15px;
    line-height: 1.45;
    white-space: nowrap;
  }
  .address {
    position: absolute;
    left: 44px;
    bottom: 44px;
    color: var(--ink-on-blue);
    font-weight: 300;
    font-style: normal;
    font-size: 21px;
    line-height: 1.35;
    white-space: nowrap;
  }

  /* Back side */
  .card--back {
    background: linear-gradient(160deg, var(--blue-light) 0%, var(--blue-mid) 45%, var(--blue-deep) 100%);
    display: flex;
    align-items: center;
    justify-content: center;
  }
  .card--back .wordmark { color: var(--ink-on-blue); white-space: nowrap; }
  .card--back .wordmark__name { font-size: 38px; }
  .card--back .wordmark__suffix { font-size: 27px; }
  .card--back .wordmark__mark { background: var(--ink-on-blue); width: 16px; height: 16px; }
</style>
</head>
<body>
<main class="canvas">
  <section class="card card--front" aria-label="Business card front">
    <div class="blue-band"></div>
    <div class="wordmark">
      <span class="wordmark__mark"></span>
      <span class="wordmark__name">Stonemarsh</span>
      <span class="wordmark__suffix">Financial LLC</span>
    </div>
    <div class="holder">
      <p class="holder__name">Daniel R Hale</p>
      <p class="holder__title">Managing Director</p>
    </div>
    <div class="contact">
      <p>(1) 214-555-0148</p>
      <p>danielrhale@mail.com</p>
    </div>
    <address class="address">
      <p>4180 Harwell Creek Road</p>
      <p>Brookvale, TX, 75091</p>
    </address>
  </section>

  <section class="card card--back" aria-label="Business card back">
    <div class="wordmark">
      <span class="wordmark__mark"></span>
      <span class="wordmark__name">Stonemarsh</span>
      <span class="wordmark__suffix">Financial LLC</span>
    </div>
  </section>
</main>
</body>
</html>
```